Stationery Design Project for High End Wealth Management Firm

We need a stationery design for our high-end wealth management firm. Our clientele are affluent and our brand is built around providing investment services with world-class service.

The final concepts should provide a business card, letterhead, and envelope.

We like the idea of having text on the front and back and we MUST have black front and back business cards.
For the business card we have the following that needs to be included:
Company Logo & Tagline
Employee Name
Employee title
Employee Email
Website
2 seperate office cities, addresses, and phone numbers
Financial disclosure (small print)

Having black envelopes would be neat, but black is not a must for the envelopes.
Updates

Project Deadline Extended
Reason: To give the concept one more day of revisions.

Project Deadline Extended
Reason: To allow for more concepts and designs.

Target Market(s)

High Net Worth

Industry/Entity Type

Business

Requirements
Must have
• The following disclosure must be on the back of the card in small print:

Investment Advisory Services offered through Harrowfield Asset Partners LLC, a NFR Registered Investment Advisor. Vantory Wealth Management LLC is not affiliated with Harrowfield Asset Partners LLC.

Black business cards are also a must have.

Please utilize each of the 3 components of our logo in the design.

Please use our white background logo elements when designing our letterhead if you need them.
Nice to have
• Please use our company colors when designing. Utilize a combination of the elements of our logo that we have attached.

We are going to be printing our business cards on letterpress.

```html
<!DOCTYPE html>
<html lang="en">
<head>
<meta charset="utf-8">
<title>Vantory Wealth Management – Envelope</title>
<link rel="stylesheet" href="https://fonts.googleapis.com/css2?family=Open+Sans:wght@400;600&display=swap">
<style>
  :root {
    --ink: #231f20;
    --gold: #d2a265;
    --gold-deep: #c08848;
    --paper: #ffffff;
    --edge: #b9b9b9;
    --text: #333333;
    --muted: #8d8d8d;
    --faint: #ece4da;
  }
  * { margin: 0; padding: 0; box-sizing: border-box; }
  html, body { width: 1200px; height: 964px; overflow: hidden; background: #ffffff; }
  body { position: relative; font-family: "Open Sans", Arial, sans-serif; color: var(--text); }

  .envelope { position: absolute; left: 0; top: 0; width: 1200px; height: 964px; }

  .flap { position: absolute; left: 0; top: 0; width: 1200px; height: 160px; }

  .flap-brand {
    position: absolute; left: 0; right: 0; top: 72px;
    text-align: center;
    transform: rotate(180deg);
    font-weight: 600; font-size: 26px; letter-spacing: 3px;
    color: var(--gold);
  }
  .flap-brand .mark {
    display: inline-block; width: 30px; height: 30px; border-radius: 50%;
    background: var(--gold); vertical-align: middle; margin-right: 14px;
  }

  .gold-band {
    position: absolute; left: 18px; top: 156px; width: 1164px; height: 126px;
    background: var(--gold);
    border-left: 1px solid var(--edge); border-right: 1px solid var(--edge);
  }

  .body-panel {
    position: absolute; left: 18px; top: 282px; width: 1164px; height: 616px;
    background: var(--paper);
    border: 1px solid var(--edge); border-top: none;
    box-shadow: inset 0 18px 26px -14px rgba(0,0,0,0.12), inset 0 -18px 26px -14px rgba(0,0,0,0.10);
  }

  .bottom-strip {
    position: absolute; left: 18px; top: 898px; width: 1164px; height: 15px;
    background: var(--gold-deep);
  }

  .watermark {
    position: absolute; left: 0; right: 0; top: 520px;
    text-align: center;
    font-weight: 600; font-size: 40px; letter-spacing: 6px;
    color: var(--faint);
  }

  .brand {
    position: absolute; left: 40px; top: 790px;
    display: flex; align-items: center; gap: 16px;
    font-weight: 600; font-size: 28px; letter-spacing: 2px;
    color: var(--muted);
  }
  .brand .mark {
    width: 46px; height: 46px; border-radius: 50%; background: var(--gold);
  }

  .contact {
    position: absolute; left: 955px; top: 745px;
    font-size: 13.5px; line-height: 17px; color: var(--text);
  }
  .contact-row { display: grid; grid-template-columns: 66px 12px auto; }
  .contact-row + .contact-row { margin-top: 27px; }
  .contact-row.phone { margin-top: 37px; }
</style>
</head>
<body>
<main class="envelope">
  <svg class="flap" viewBox="0 0 1200 160" aria-hidden="true">
    <path d="M18 120 Q18 116 30 114 L580 36 Q600 34 620 36 L1170 114 Q1182 116 1182 120 L1182 157 L18 157 Z" fill="#231f20"/>
  </svg>
  <div class="flap-brand"><span class="mark"></span>VANTORY WEALTH MANAGEMENT</div>

  <div class="gold-band"></div>
  <section class="body-panel"></section>
  <div class="bottom-strip"></div>

  <div class="watermark">VANTORY</div>

  <div class="brand"><span class="mark"></span><span>VANTORY WEALTH MANAGEMENT</span></div>

  <address class="contact" style="font-style: normal;">
    <div class="contact-row"><span>Office</span><span>:</span><span>Loreum Ipsum Dollar,<br>Loreum Ipsum</span></div>
    <div class="contact-row"><span>Address</span><span>:</span><span>Loreum Ipsum Dollar,<br>Loreum Ipsum</span></div>
    <div class="contact-row phone"><span>Phone</span><span>:</span><span>+9714 555 0192</span></div>
  </address>
</main>
</body>
</html>
```